Business Card Design Project

We are a construction company in Orange County, CA. We need a two sided business card. We would like the back to be our logo with web URL. Front should included Name, title, address, phone, fax and email address.

our address is
627 West Dorrance Blvd, Suite 308
Corvale, CA 92718

Our logo files are attached.

Construction

```html
<!DOCTYPE html>
<html lang="en">
<head>
<meta charset="utf-8">
<title>Brixwell Business Card</title>
<link href="https://fonts.googleapis.com/css2?family=Open+Sans:wght@400;700;800&display=swap" rel="stylesheet">
<style>
  :root {
    --backdrop: #c8925f;
    --card: #ffffff;
    --card-edge: #d9d4cf;
    --navy: #1d4c7c;
    --ink: #3a3a3a;
    --muted: #5a5a5a;
  }
  * { box-sizing: border-box; margin: 0; padding: 0; }
  html, body { width: 1200px; height: 398px; overflow: hidden; }
  body {
    background: var(--backdrop);
    font-family: "Open Sans", Arial, sans-serif;
    position: relative;
  }
  .card {
    position: absolute;
    top: 44px;
    width: 526px;
    height: 298px;
    background: var(--card);
    border: 1px solid var(--card-edge);
    border-radius: 22px;
    overflow: hidden;
  }
  .card-front { left: 43px; }
  .card-back { left: 603px; }

  .brand-name {
    position: absolute;
    color: var(--navy);
    font-weight: 800;
    letter-spacing: -1px;
    line-height: 1;
  }
  .card-front .brand-name { left: 60px; top: 22px; font-size: 62px; }
  .card-back .brand-name { left: 0; right: 0; top: 99px; text-align: center; font-size: 68px; }

  .contact-list { position: absolute; left: 0; top: 152px; }
  .contact-row {
    display: flex;
    align-items: flex-start;
    margin-bottom: 4px;
  }
  .contact-row.address { margin-bottom: 9px; }
  .contact-label {
    width: 59px;
    height: 15px;
    background: var(--navy);
    color: #fff;
    font-size: 12px;
    line-height: 15px;
    text-align: right;
    padding-right: 4px;
    margin-top: 1px;
  }
  .contact-value {
    margin-left: 9px;
    color: var(--ink);
    font-size: 13.5px;
    line-height: 16px;
  }

  .person {
    position: absolute;
    right: 30px;
    top: 191px;
    text-align: right;
    color: var(--navy);
  }
  .person-name { font-size: 18px; font-weight: 700; line-height: 24px; }
  .person-title { font-size: 16px; line-height: 22px; }

  .web-address {
    position: absolute;
    left: 0; right: 0;
    top: 213px;
    text-align: center;
    color: var(--muted);
    font-size: 17px;
    letter-spacing: 1.5px;
  }
</style>
</head>
<body>
  <section class="card card-front" aria-label="Card front">
    <div class="brand-name">BRIXWELL</div>

    <div class="contact-list">
      <div class="contact-row address">
        <span class="contact-label">Address</span>
        <span class="contact-value">627 West Dorrance Blvd<br>Suite 308, Corvale, CA&nbsp; 92718</span>
      </div>
      <div class="contact-row">
        <span class="contact-label">Phone</span>
        <span class="contact-value">01-555-0142</span>
      </div>
      <div class="contact-row">
        <span class="contact-label">Fax</span>
        <span class="contact-value">01-555-0143</span>
      </div>
      <div class="contact-row">
        <span class="contact-label">Email</span>
        <span class="contact-value">info@brixwellmail.com</span>
      </div>
      <div class="contact-row">
        <span class="contact-label">Web</span>
        <span class="contact-value">www.brixwell.com</span>
      </div>
    </div>

    <div class="person">
      <div class="person-name">Your Name</div>
      <div class="person-title">Title</div>
    </div>
  </section>

  <section class="card card-back" aria-label="Card back">
    <div class="brand-name">BRIXWELL</div>
    <div class="web-address">www.brixwell.com</div>
  </section>
</body>
</html>
```